Corvane Lending Partners. Professional and Established Company

A full service finance company specializing in obtaining capital for small business. Business Lending advisor, helping small business owners access the capital they need to launch, grow, or sustain their business. Many of our programs offer flexible guidelines to overcome common obstacles such as credit score, credit history, and time in business, financials, and industry type. Our streamlined funding process makes getting a business loan, business line of credit, stated income commercial real estate loan, a smooth and stress free experience.SOME OF THE MOST COMMON NEEDS FOR BUSINESS CAPITAL:• Working Capital• Debt Consolidations (loans, merchant cash advances, etc.)• Payroll• Operating Expenses• Inventory• Equipment Financing• Commercial Real Estate (Purchase, Fix & Flip, Rehab, Renovations)• Business Acquisitions• Business ExpansionWe like the websites:www.quillmorecf.com they are in the same industry and provide the same servicesWe are wanting to be able to update when we do press releases and such using Word Press. Our look should be very professional and we will be adding Our Team Professional Bios and Headshots.

Industry/Entity Type

Finance

Number of Pages Required

5+ page

Font styles to use
Serif
Sans Serif

Requirements
Must have
• We want to copy quillmorecf.com
• We need:
• Home Page
• About Us
• Loan Programs
• Loan Criteria
• News
• Apply Now
• Contact
Nice to have
• See quillmorecf.com
Should not have
• Need professional design. Nothing bright or abstract

```html
<!DOCTYPE html>
<html lang="en">
<head>
<meta charset="utf-8">
<title>Corvane Lending Partners</title>
<link rel="stylesheet" href="https://fonts.googleapis.com/css2?family=PT+Serif:wght@400;700&family=Roboto:wght@400;500;700&display=swap">
<style>
:root{
  --blue:#2b67b2;
  --blue-dark:#1f539a;
  --ink:#2b2b2b;
  --muted:#777b80;
  --line:#d9dde2;
  --footer:#1f2022;
  --footer-text:#c9cbce;
  --white:#ffffff;
}
*{box-sizing:border-box;margin:0;padding:0}
html,body{width:1200px;height:4276px;overflow:hidden;background:var(--white)}
body{position:relative;font-family:"Roboto",Arial,sans-serif;color:var(--ink)}
.abs{position:absolute}

/* header */
.topline{left:0;top:0;width:1200px;height:4px;background:var(--blue)}
.brand{left:114px;top:44px;font-family:"PT Serif",Georgia,serif;font-size:30px;color:var(--blue);font-weight:400;letter-spacing:.5px}
.contact-strip{right:114px;top:32px;font-size:13px;color:var(--muted);display:flex;align-items:center;gap:10px}
.contact-strip svg{width:13px;height:13px;fill:var(--blue)}
.contact-strip .sep{width:1px;height:14px;background:var(--line);margin:0 8px}
.main-nav{right:114px;top:84px;display:flex;gap:22px;font-size:15px;font-weight:500;color:#222;letter-spacing:.2px}

/* hero */
.hero{left:0;top:134px;width:1200px;height:556px;background:linear-gradient(100deg,#dfe7ee 0%,#b9c8d6 35%,#7d8f9f 60%,#3d4a57 100%)}
.hero-title{left:114px;top:318px;font-family:"PT Serif",Georgia,serif;font-size:40px;color:var(--blue-dark);font-weight:700;letter-spacing:1px}
.hero-text{left:114px;top:386px;width:440px;font-size:15px;line-height:26px;color:#1d2b3a;font-weight:500}
.btn-solid{background:var(--blue);color:var(--white);font-size:14px;font-weight:700;letter-spacing:.5px;display:flex;align-items:center;justify-content:center;gap:6px}
.hero-btn{left:114px;top:458px;width:168px;height:46px}
.slide-arrow{width:38px;height:38px;border-radius:50%;background:rgba(60,60,60,.55);display:flex;align-items:center;justify-content:center}
.slide-arrow svg{width:14px;height:14px;stroke:#fff;fill:none;stroke-width:2.5}

/* welcome */
.section-title{left:0;width:1200px;text-align:center;font-family:"PT Serif",Georgia,serif;font-size:40px;color:var(--blue);font-weight:400;text-transform:uppercase}
.welcome-text{left:280px;top:868px;width:640px;text-align:center;font-size:13px;line-height:24px;color:var(--muted)}
.spec-title{left:114px;top:966px;width:520px;font-family:"PT Serif",Georgia,serif;font-size:26px;font-weight:400;line-height:38px;color:#222;text-transform:uppercase;white-space:nowrap}
.spec-text{left:114px;top:1078px;width:480px;font-size:13px;line-height:22px;color:var(--muted)}
.btn-outline{border:2px solid var(--blue);color:var(--blue);background:var(--white);font-size:13px;font-weight:700;letter-spacing:.5px;display:flex;align-items:center;justify-content:center;gap:6px}
.spec-btn{left:114px;top:1238px;width:156px;height:42px}
.video-frame{left:638px;top:978px;width:456px;height:304px}
.video-still{left:650px;top:990px;width:432px;height:280px;background:linear-gradient(135deg,#e7edf3 0%,#b8c6d4 50%,#6f8397 100%)}
.play{left:838px;top:1104px;width:56px;height:56px;border-radius:50%;background:var(--white);display:flex;align-items:center;justify-content:center;box-shadow:0 2px 6px rgba(0,0,0,.25)}

/* careers */
.careers-photo{left:0;top:1388px;width:600px;height:467px;background:linear-gradient(120deg,#d8dfe6 0%,#a9b3bd 45%,#5b5f66 100%)}
.careers-panel{left:600px;top:1388px;width:600px;height:467px;background:var(--blue)}
.careers-title{left:664px;top:1454px;width:480px;font-family:"PT Serif",Georgia,serif;font-size:38px;font-weight:400;line-height:52px;color:var(--white);text-transform:uppercase}
.careers-text{left:664px;top:1590px;width:430px;font-size:13px;line-height:22px;color:#e3ecf7}
.careers-btn{left:664px;top:1734px;width:182px;height:42px;border:2px solid var(--white);color:var(--white);font-size:13px;font-weight:700;display:flex;align-items:center;justify-content:center;gap:6px}

/* services */
.service-card{width:302px;height:365px;background:var(--white);box-shadow:0 1px 8px rgba(0,0,0,.18)}
.service-card .photo{position:absolute;left:6px;top:6px;width:290px;height:188px}
.service-card h3{position:absolute;left:0;top:228px;width:100%;text-align:center;font-family:"PT Serif",Georgia,serif;font-size:19px;font-weight:700;letter-spacing:1px;color:#222;text-transform:uppercase}
.service-card p{position:absolute;left:18px;top:268px;width:266px;text-align:center;font-size:12.5px;line-height:22px;color:var(--muted)}
.service-card .btn-outline{position:absolute;left:81px;top:346px;width:140px;height:38px;border:1px solid var(--line);box-shadow:0 1px 3px rgba(0,0,0,.12)}

/* team */
.team-band{left:0;top:3460px;width:1200px;height:413px;background:linear-gradient(115deg,#2b67b2 0%,#235aa2 50%,#2d6bb6 100%)}
.team-title{top:3545px;color:var(--white)}
.headshot{width:132px;height:132px;border-radius:50%;border:4px solid var(--white);background:linear-gradient(160deg,#d9dee4,#8995a3)}
.member-name{font-family:"PT Serif",Georgia,serif;font-size:22px;letter-spacing:1px;color:var(--white);text-transform:uppercase}
.member-role{font-size:14px;font-weight:700;color:var(--white)}
.member-bio{width:330px;font-size:13px;line-height:22px;color:#dce7f5}
.team-arrow svg{width:22px;height:22px;stroke:#fff;fill:none;stroke-width:3}

/* footer */
.site-footer{left:0;top:3873px;width:1200px;height:403px;background:var(--footer)}
.footer-brand{left:114px;top:3990px;font-family:"PT Serif",Georgia,serif;font-size:24px;color:#5d95d8}
.social{display:flex;gap:14px;left:140px;top:4082px}
.social span{width:34px;height:34px;border-radius:50%;border:2px solid #e0e0e0}
.footer-col h4{font-size:15px;font-weight:700;color:var(--white);letter-spacing:.5px;margin-bottom:16px;text-transform:uppercase}
.footer-col li{list-style:none;font-size:12.5px;color:var(--footer-text);line-height:29px;display:flex;align-items:center;gap:8px}
.footer-col li::before{content:"";width:0;height:0;border-left:5px solid var(--footer-text);border-top:4px solid transparent;border-bottom:4px solid transparent}
.contact-item{display:flex;gap:14px;font-size:12.5px;line-height:20px;color:var(--footer-text);margin-bottom:20px}
.contact-item svg{width:15px;height:15px;fill:var(--white);flex:none;margin-top:2px}
.footer-rule{left:114px;top:4192px;width:972px;height:1px;background:#45474a}
.copyright{left:0;top:4222px;width:1200px;text-align:center;font-size:13px;color:var(--footer-text)}
</style>
</head>
<body>

<header>
  <div class="abs topline"></div>
  <div class="abs brand">Corvane Lending Partners</div>
  <div class="abs contact-strip">
    <svg viewBox="0 0 24 24"><path d="M6.6 10.8a15.1 15.1 0 0 0 6.6 6.6l2.2-2.2c.3-.3.7-.4 1-.2 1.1.4 2.3.6 3.6.6.6 0 1 .4 1 1V20c0 .6-.4 1-1 1A17 17 0 0 1 3 4c0-.6.4-1 1-1h3.5c.6 0 1 .4 1 1 0 1.3.2 2.5.6 3.6.1.3 0 .7-.2 1z"/></svg>
    <span>(+1) 555 014 2290</span>
    <span class="sep"></span>
    <svg viewBox="0 0 24 24"><path d="M2 5h20v14H2z M2 5l10 8 10-8" fill="none" stroke="#2b67b2" stroke-width="2"/></svg>
    <span>info@corvanelending.com</span>
  </div>
  <nav class="abs main-nav">
    <span>HOME</span><span>ABOUT</span><span>LOAN PROGRAMS</span><span>LOAN CRITERIA</span><span>NEWS</span><span>APPLY NOW</span><span>CONTACT</span>
  </nav>
</header>

<section>
  <div class="abs hero" role="img" aria-label="Businessman in glasses working on a laptop in a bright office with colleagues behind"></div>
  <div class="abs hero-title">CORVANE LENDING</div>
  <p class="abs hero-text">At vero eos et accusamus et iusto odio dignissimos ducimus qui blanditiis praesentium voluptatum deleniti atque</p>
  <div class="abs btn-solid hero-btn">READ MORE <svg width="13" height="13" viewBox="0 0 16 16"><circle cx="8" cy="8" r="7.5" fill="#fff"/><path d="M6.5 4.5 10 8l-3.5 3.5" stroke="#2b67b2" stroke-width="2" fill="none"/></svg></div>
  <div class="abs slide-arrow" style="left:22px;top:393px"><svg viewBox="0 0 16 16"><path d="M10 3 5 8l5 5"/></svg></div>
  <div class="abs slide-arrow" style="left:1140px;top:393px;background:none"><svg viewBox="0 0 16 16"><path d="M6 3l5 5-5 5"/></svg></div>
</section>

<section>
  <h2 class="abs section-title" style="top:792px">Welcome to Corvane</h2>
  <p class="abs welcome-text">Lorem ipsum dolor sit amet, consectetur adipisicing elit, sed do eiusmod tempor incididunt ut labore et dolore magna aliqua. Ut enim ad minim veniam, quis nostrud exercitation ullamco laboris nisi ut aliquip ex ea commodo consequat.</p>
  <h3 class="abs spec-title">We are specializing in obtaining<br>capital for small business.</h3>
  <p class="abs spec-text">Nemo enim ipsam voluptatem quia voluptas sit aspernatur aut odit aut fugit, sed quia consequuntur magni dolores eos qui ratione. Voluptatem sequi nesciunt. Neque porro quisquam est, qui dolorem ipsum quia dolor sit amet, consectetur, adipisci velit, sed quia non numquam eius modi tempora incidunt ut labore et dolore magnam aliquam quaerat voluptatem.</p>
  <div class="abs btn-outline spec-btn">READ MORE <svg width="13" height="13" viewBox="0 0 16 16"><circle cx="8" cy="8" r="7.5" fill="#2b67b2"/><path d="M6.5 4.5 10 8l-3.5 3.5" stroke="#fff" stroke-width="2" fill="none"/></svg></div>
  <svg class="abs video-frame" viewBox="0 0 456 304" fill="none" stroke="#2b67b2" stroke-width="4">
    <path d="M2 40V2h40"/><path d="M414 2h40v38"/><path d="M2 264v38h40"/><path d="M414 302h40v-38"/>
  </svg>
  <div class="abs video-still" role="img" aria-label="Video still of two colleagues reviewing charts at a desk"></div>
  <div class="abs play"><svg width="20" height="22" viewBox="0 0 20 22"><path d="M3 2l15 9-15 9z" fill="#2b67b2"/></svg></div>
</section>

<section>
  <div class="abs careers-photo" role="img" aria-label="Business owners shaking hands with an advisor across a table"></div>
  <div class="abs careers-panel"></div>
  <h2 class="abs careers-title">Start your careers with Corvane</h2>
  <p class="abs careers-text">At vero eos et accusamus et iusto odio dignissimos ducimus qui blanditiis praesentium voluptatum deleniti atque corrupti quos dolores et quas molestias excepturi sint occaecati cupiditate non provident, similique sunt in culpa qui officia deserunt mollitia animi.</p>
  <div class="abs careers-btn">JOIN US NOW <svg width="13" height="13" viewBox="0 0 16 16"><circle cx="8" cy="8" r="7.5" fill="#fff"/><path d="M6.5 4.5 10 8l-3.5 3.5" stroke="#2b67b2" stroke-width="2" fill="none"/></svg></div>
</section>

<section>
  <h2 class="abs section-title" style="top:1966px">Our Services</h2>

  <article class="abs service-card" style="left:114px;top:2066px">
    <div class="photo" role="img" aria-label="Trading desk with several monitors" style="background:linear-gradient(135deg,#c9d6e4,#5f7893)"></div>
    <h3>Working Capital</h3>
    <p>At vero eost et accusamus et iusto odio dignissimos ducimus qui blanditiis praesentium voluptatum</p>
    <div class="btn-outline">READ MORE <svg width="13" height="13" viewBox="0 0 16 16"><circle cx="8" cy="8" r="7.5" fill="#2b67b2"/><path d="M6.5 4.5 10 8l-3.5 3.5" stroke="#fff" stroke-width="2" fill="none"/></svg></div>
  </article>
  <article class="abs service-card" style="left:450px;top:2066px">
    <div class="photo" role="img" aria-label="Dealership showroom with a customer meeting" style="background:linear-gradient(135deg,#e3e5e8,#8a929b)"></div>
    <h3>Debt Consolidations</h3>
    <p>At vero eost et accusamus et iusto odio dignissimos ducimus qui blanditiis praesentium voluptatum</p>
    <div class="btn-outline">READ MORE <svg width="13" height="13" viewBox="0 0 16 16"><circle cx="8" cy="8" r="7.5" fill="#2b67b2"/><path d="M6.5 4.5 10 8l-3.5 3.5" stroke="#fff" stroke-width="2" fill="none"/></svg></div>
  </article>
  <article class="abs service-card" style="left:786px;top:2066px">
    <div class="photo" role="img" aria-label="Hands passing a paycheck" style="background:linear-gradient(135deg,#d7dbe0,#4a4f57)"></div>
    <h3>Payroll</h3>
    <p>At vero eost et accusamus et iusto odio dignissimos ducimus qui blanditiis praesentium voluptatum</p>
    <div class="btn-outline">READ MORE <svg width="13" height="13" viewBox="0 0 16 16"><circle cx="8" cy="8" r="7.5" fill="#2b67b2"/><path d="M6.5 4.5 10 8l-3.5 3.5" stroke="#fff" stroke-width="2" fill="none"/></svg></div>
  </article>

  <article class="abs service-card" style="left:114px;top:2514px">
    <div class="photo" role="img" aria-label="Calculator and paperwork on a desk" style="background:linear-gradient(135deg,#eef0f2,#a3a8ae)"></div>
    <h3>Operating Expenses</h3>
    <p>At vero eost et accusamus et iusto odio dignissimos ducimus qui blanditiis praesentium voluptatum</p>
    <div class="btn-outline">READ MORE <svg width="13" height="13" viewBox="0 0 16 16"><circle cx="8" cy="8" r="7.5" fill="#2b67b2"/><path d="M6.5 4.5 10 8l-3.5 3.5" stroke="#fff" stroke-width="2" fill="none"/></svg></div>
  </article>
  <article class="abs service-card" style="left:450px;top:2514px">
    <div class="photo" role="img" aria-label="Warehouse staff checking inventory between shelves" style="background:linear-gradient(135deg,#b8a68c,#4e5560)"></div>
    <h3>Inventory</h3>
    <p>At vero eost et accusamus et iusto odio dignissimos ducimus qui blanditiis praesentium voluptatum</p>
    <div class="btn-outline">READ MORE <svg width="13" height="13" viewBox="0 0 16 16"><circle cx="8" cy="8" r="7.5" fill="#2b67b2"/><path d="M6.5 4.5 10 8l-3.5 3.5" stroke="#fff" stroke-width="2" fill="none"/></svg></div>
  </article>
  <article class="abs service-card" style="left:786px;top:2514px">
    <div class="photo" role="img" aria-label="Hand stacking coins on a table" style="background:linear-gradient(135deg,#c7b9a8,#5a4a3c)"></div>
    <h3>Equipment Financing</h3>
    <p>At vero eost et accusamus et iusto odio dignissimos ducimus qui blanditiis praesentium voluptatum</p>
    <div class="btn-outline">READ MORE <svg width="13" height="13" viewBox="0 0 16 16"><circle cx="8" cy="8" r="7.5" fill="#2b67b2"/><path d="M6.5 4.5 10 8l-3.5 3.5" stroke="#fff" stroke-width="2" fill="none"/></svg></div>
  </article>

  <article class="abs service-card" style="left:114px;top:2961px">
    <div class="photo" role="img" aria-label="Agent showing a house to a couple" style="background:linear-gradient(135deg,#c8d3c6,#6b7a70)"></div>
    <h3>Real Estate</h3>
    <p>At vero eost et accusamus et iusto odio dignissimos ducimus qui blanditiis praesentium voluptatum</p>
    <div class="btn-outline">READ MORE <svg width="13" height="13" viewBox="0 0 16 16"><circle cx="8" cy="8" r="7.5" fill="#2b67b2"/><path d="M6.5 4.5 10 8l-3.5 3.5" stroke="#fff" stroke-width="2" fill="none"/></svg></div>
  </article>
  <article class="abs service-card" style="left:450px;top:2961px">
    <div class="photo" role="img" aria-label="Handshake over signed documents" style="background:linear-gradient(135deg,#e6e8eb,#7a8591)"></div>
    <h3>Business Acquisitions</h3>
    <p>At vero eost et accusamus et iusto odio dignissimos ducimus qui blanditiis praesentium voluptatum</p>
    <div class="btn-outline">READ MORE <svg width="13" height="13" viewBox="0 0 16 16"><circle cx="8" cy="8" r="7.5" fill="#2b67b2"/><path d="M6.5 4.5 10 8l-3.5 3.5" stroke="#fff" stroke-width="2" fill="none"/></svg></div>
  </article>
  <article class="abs service-card" style="left:786px;top:2961px">
    <div class="photo" role="img" aria-label="Hand touching a glowing world network" style="background:linear-gradient(135deg,#2c4f86,#0d1c36)"></div>
    <h3>Business Expansion</h3>
    <p>At vero eost et accusamus et iusto odio dignissimos ducimus qui blanditiis praesentium voluptatum</p>
    <div class="btn-outline">READ MORE <svg width="13" height="13" viewBox="0 0 16 16"><circle cx="8" cy="8" r="7.5" fill="#2b67b2"/><path d="M6.5 4.5 10 8l-3.5 3.5" stroke="#fff" stroke-width="2" fill="none"/></svg></div>
  </article>
</section>

<section>
  <div class="abs team-band"></div>
  <h2 class="abs section-title team-title">Our Team</h2>
  <div class="abs team-arrow" style="left:36px;top:3694px"><svg viewBox="0 0 16 16"><path d="M10 3 5 8l5 5"/></svg></div>
  <div class="abs team-arrow" style="left:1120px;top:3694px"><svg viewBox="0 0 16 16"><path d="M6 3l5 5-5 5"/></svg></div>

  <div class="abs headshot" role="img" aria-label="Headshot of a team member" style="left:120px;top:3640px"></div>
  <div class="abs member-name" style="left:278px;top:3648px">Maren Halloway</div>
  <div class="abs member-role" style="left:278px;top:3686px">CEO, Founder.</div>
  <p class="abs member-bio" style="left:278px;top:3716px">At vero eost et accusamus et iusto odio dignissimos ducimus qui blanditiis praesentium</p>

  <div class="abs headshot" role="img" aria-label="Headshot of a team member" style="left:636px;top:3640px"></div>
  <div class="abs member-name" style="left:794px;top:3648px">Tobias Renwick</div>
  <div class="abs member-role" style="left:794px;top:3686px">Co-Founder, Manager.</div>
  <p class="abs member-bio" style="left:794px;top:3716px">At vero eost et accusamus et iusto odio dignissimos ducimus qui blanditiis praesentium</p>
</section>

<footer>
  <div class="abs site-footer"></div>
  <div class="abs footer-brand">Corvane Lending Partners</div>
  <div class="abs social"><span></span><span></span><span></span><span></span></div>

  <div class="abs footer-col" style="left:436px;top:3960px">
    <h4>Quick Links</h4>
    <ul><li>Home</li><li>About Us</li><li>My Services</li><li>News</li><li>Contact Me</li></ul>
  </div>
  <div class="abs footer-col" style="left:633px;top:3960px">
    <h4>Our Services</h4>
    <ul><li>Loan Programs</li><li>Loan Criteria</li><li>Debt Consolidations</li><li>Operating Expenses</li><li>Inventory</li></ul>
  </div>
  <div class="abs footer-col" style="left:855px;top:3960px">
    <h4>Contact Details</h4>
    <div class="contact-item"><svg viewBox="0 0 24 24"><path d="M12 2a7 7 0 0 0-7 7c0 5 7 13 7 13s7-8 7-13a7 7 0 0 0-7-7zm0 9.5A2.5 2.5 0 1 1 12 6a2.5 2.5 0 0 1 0 5.5z"/></svg><span>240 Harbor Commerce Way, Suite 210<br>Linden Ridge, PA 17502</span></div>
    <div class="contact-item"><svg viewBox="0 0 24 24"><path d="M6.6 10.8a15.1 15.1 0 0 0 6.6 6.6l2.2-2.2c.3-.3.7-.4 1-.2 1.1.4 2.3.6 3.6.6.6 0 1 .4 1 1V20c0 .6-.4 1-1 1A17 17 0 0 1 3 4c0-.6.4-1 1-1h3.5c.6 0 1 .4 1 1 0 1.3.2 2.5.6 3.6.1.3 0 .7-.2 1z"/></svg><span>(+1) 555 014 2290</span></div>
    <div class="contact-item"><svg viewBox="0 0 24 24"><path d="M2 5h20v14H2zm2 2v.5l8 6 8-6V7z"/></svg><span>info@corvanelending.com</span></div>
  </div>

  <div class="abs footer-rule"></div>
  <p class="abs copyright">Copyrights © 2018 Corvane Lending Partners. All Rights Reserved.</p>
</footer>

</body>
</html>
```